Tovel & Associates - London New Letting and Property Management Company *

Tovel & Associates LTD is a new company based in London, and works with brand new residential property in the city centre.

We are aiming to have 1000 new properties a year.

We are looking for something modern and minimalistic :
Logo ,Monogram, Paper Head and Business Card.

Target Market(s)

Internation landlords

Industry/Entity Type

Real Estate

Logo Text

Tovel & Associates

Colors

Designer to choose colors to be used in the design.

Requirements
Nice to have
• A particular monogram with "TA"
Should not have
• Little House over the logo

```html
<!DOCTYPE html>
<html lang="en">
<head>
<meta charset="UTF-8">
<title>Tovel &amp; Associates LTD – Business Card</title>
<link href="https://fonts.googleapis.com/css2?family=Montserrat:wght@400;500;700&display=swap" rel="stylesheet">
<style>
  :root {
    --backdrop: #161616;
    --card: #262626;
    --card-edge: #2e2e2e;
    --brand-blue: #1677c6;
    --ink-light: #ffffff;
    --ink-soft: #e6e6e6;
  }
  * { margin: 0; padding: 0; box-sizing: border-box; }
  html, body {
    width: 1200px; height: 900px; overflow: hidden;
    background: var(--backdrop);
    font-family: "Montserrat", Arial, sans-serif;
  }
  .stage {
    position: relative; width: 1200px; height: 900px;
    display: flex; flex-direction: column; align-items: center; justify-content: center;
    gap: 40px;
  }
  .card {
    position: relative; width: 620px; height: 354px;
    background: linear-gradient(135deg, var(--card-edge), var(--card));
    border-bottom: 6px solid var(--brand-blue);
    box-shadow: 0 14px 30px rgba(0,0,0,.45);
  }
  .wordmark {
    display: flex; align-items: center; gap: 12px;
    color: var(--ink-light); font-weight: 700; letter-spacing: .3px;
  }
  .wordmark__square { width: 20px; height: 20px; background: var(--brand-blue); flex: none; }
  .card--front { display: flex; align-items: center; justify-content: center; }
  .card--front .wordmark { font-size: 30px; }
  .card--back { display: flex; align-items: center; }
  .card--back .brand-side { width: 50%; display: flex; justify-content: center; }
  .card--back .wordmark { font-size: 21px; gap: 10px; }
  .card--back .wordmark__square { width: 16px; height: 16px; }
  .divider { width: 2px; height: 200px; background: var(--brand-blue); }
  .contact-side { padding-left: 34px; color: var(--ink-soft); }
  .person__name { color: var(--brand-blue); font-weight: 700; font-size: 21px; letter-spacing: .5px; }
  .person__role { font-size: 15px; margin: 2px 0 14px; }
  .contact-list { list-style: none; font-size: 15px; line-height: 1.55; }
  .contact-list li { display: flex; align-items: center; gap: 10px; }
  .contact-list svg { width: 13px; height: 13px; flex: none; }
  .contact-list .accent { color: var(--brand-blue); }
  .address { font-size: 15px; line-height: 1.45; margin-top: 10px; }
</style>
</head>
<body>
<main class="stage">
  <section class="card card--front">
    <div class="wordmark"><span class="wordmark__square"></span>Tovel &amp; Associates LTD</div>
  </section>

  <section class="card card--back">
    <div class="brand-side">
      <div class="wordmark"><span class="wordmark__square"></span>Tovel &amp; Associates LTD</div>
    </div>
    <div class="divider"></div>
    <div class="contact-side">
      <p class="person__name">DANIEL HART</p>
      <p class="person__role">Founder</p>
      <ul class="contact-list">
        <li><svg viewBox="0 0 12 12" fill="none" stroke="#1677c6" stroke-width="1.2"><rect x="3" y="1" width="6" height="10" rx="1"/><line x1="5" y1="9" x2="7" y2="9"/></svg>020. 7946. 0182</li>
        <li><svg viewBox="0 0 12 12" fill="none" stroke="#1677c6" stroke-width="1.2"><path d="M3 1.5 L5 4 L4 5.2 Q5 7.5 7 8.2 L8.2 7 L10.5 9 L9.2 10.5 Q4.5 10 1.5 3 Z"/></svg>020. 7946. 0455</li>
        <li><svg viewBox="0 0 12 12" fill="none" stroke="#1677c6" stroke-width="1.2"><rect x="1" y="2.5" width="10" height="7"/><polyline points="1,2.5 6,6.5 11,2.5"/></svg>info@tovelassociates.com</li>
        <li><svg viewBox="0 0 12 12" fill="none" stroke="#1677c6" stroke-width="1.1"><circle cx="6" cy="6" r="5"/><ellipse cx="6" cy="6" rx="2.2" ry="5"/><line x1="1" y1="6" x2="11" y2="6"/></svg><span>www.<span class="accent">tovelassociates</span>.com</span></li>
      </ul>
      <p class="address">48 Harrow Lane<br>London, EC2A 4NE</p>
    </div>
  </section>
</main>
</body>
</html>
```